Commercial Loan Originator Business Card (CHANGE COLORS SCHEME)

CHANGE COLOR SCHEME - SAME DESIGN

Name Marlene Agate
Title Commercial Loan Originator
Office (800) 417-2906 x68
Direct (240) 615-2043
Email freshgreens4life@quillbox.example

Name Dale Morrow
Office (800) 417-2906 x70
Direct (410) 392-5184
Email d.morthehomeguy@quillbox.example

Name Leonard Vasko
Office (800) 417-2906 x71
Direct (215) 463-0712
Email l.vasko41@quillbox.example

Name Gwen Halsey
Office (800) 417-2906 x
Direct (202) 548-1370
Email ghalsey63@quillbox.example

Name Mirna Ashby
Office (800) 417-2906 x72
Direct (240) 871-4526
Email tristatehomelending@quillbox.example

```html
<!DOCTYPE html>
<html lang="en">
<head>
<meta charset="utf-8">
<title>Leonard Vasko – Commercial Loan Originator</title>
<link rel="stylesheet" href="https://fonts.googleapis.com/css2?family=Cinzel:wght@600&family=Poppins:wght@400&display=swap">
<style>
  :root {
    --backdrop: #8a8a8a;
    --card: #ffffff;
    --accent: #1f6f86;
    --accent-pale: #d7eaf0;
    --ink: #1f1f1f;
    --suit-navy: #1d2a52;
    --portrait-light: #f4f5f8;
  }
  * { margin: 0; padding: 0; box-sizing: border-box; }
  html, body {
    width: 1200px; height: 952px; overflow: hidden;
    background: var(--backdrop);
  }
  .business-card {
    position: absolute; left: 75px; top: 152px;
    width: 1050px; height: 649px;
    background: var(--card);
    overflow: hidden;
  }
  .corner-accent { position: absolute; left: 0; top: 0; }
  .base-band {
    position: absolute; left: 0; bottom: 0;
    width: 100%; height: 16px; background: var(--accent);
  }
  .portrait {
    position: absolute; left: 575px; top: 30px;
    width: 475px; height: 603px;
    background: radial-gradient(ellipse 34% 27% at 50% 27%, #5e4130 0%, #4e3426 55%, transparent 100%),
                linear-gradient(180deg, var(--portrait-light) 0%, var(--portrait-light) 46%, var(--suit-navy) 62%, #17213f 100%);
  }
  .identity { position: absolute; left: 47px; top: 334px; }
  .person-name {
    font-family: "Cinzel", "Times New Roman", serif;
    font-weight: 600; font-size: 46px; line-height: 50px;
    color: var(--accent); letter-spacing: 0.3px;
  }
  .job-title {
    font-family: "Poppins", Arial, sans-serif;
    font-size: 31px; line-height: 38px; color: var(--ink);
    margin-left: 3px;
  }
  .contact-list {
    position: absolute; left: 50px; top: 468px;
    list-style: none;
    font-family: "Poppins", Arial, sans-serif;
    font-size: 30px; line-height: 39px; color: var(--ink);
  }
  .contact-item { display: flex; align-items: center; gap: 16px; }
  .contact-icon { width: 28px; height: 28px; flex: none; }
</style>
</head>
<body>
  <div class="business-card">
    <svg class="corner-accent" width="680" height="175" viewBox="0 0 680 175" aria-hidden="true">
      <polygon points="0,102 0,170 668,0 650,0" fill="var(--accent-pale)"/>
      <polygon points="0,0 650,0 0,102" fill="var(--accent)"/>
    </svg>

    <div class="portrait" role="img" aria-label="Portrait photo of Leonard Vasko in a navy suit"></div>

    <div class="identity">
      <h1 class="person-name">LEONARD VASKO</h1>
      <p class="job-title">Commercial Loan Originator</p>
    </div>

    <ul class="contact-list">
      <li class="contact-item">
        <svg class="contact-icon" viewBox="0 0 28 28" aria-hidden="true">
          <path d="M7 4l4 5-2.5 2.5c1.5 3 4 5.5 7 7L18 16l5 4-2.5 4C12 23 5 16 4 7.5z" fill="none" stroke="var(--accent)" stroke-width="2.2" stroke-linejoin="round"/>
          <path d="M16 4a8 8 0 0 1 8 8M16 8a4 4 0 0 1 4 4" fill="none" stroke="var(--accent)" stroke-width="2" stroke-linecap="round"/>
        </svg>
        <span>(800) 417-2906 x71</span>
      </li>
      <li class="contact-item">
        <svg class="contact-icon" viewBox="0 0 28 28" aria-hidden="true">
          <path d="M7 4l4 5-2.5 2.5c1.5 3 4 5.5 7 7L18 16l5 4-2.5 4C12 23 5 16 4 7.5z" fill="none" stroke="var(--accent)" stroke-width="2.2" stroke-linejoin="round"/>
          <path d="M16 4a8 8 0 0 1 8 8M16 8a4 4 0 0 1 4 4" fill="none" stroke="var(--accent)" stroke-width="2" stroke-linecap="round"/>
        </svg>
        <span>(215) 463-0712 (Direct )</span>
      </li>
      <li class="contact-item">
        <svg class="contact-icon" viewBox="0 0 28 28" aria-hidden="true">
          <rect x="1" y="7" width="26" height="16" fill="var(--accent)"/>
          <path d="M1 7l13 10 13-10" fill="none" stroke="#ffffff" stroke-width="1.6"/>
        </svg>
        <span>l.vasko41@quillbox.example</span>
      </li>
    </ul>

    <div class="base-band"></div>
  </div>
</body>
</html>
```